Protective Security Officer services company needs logo and e mail stationary design

We need a logo design that compliments our vehicle wraps. We provide armed guards to the federal government. We want to use patriotic flag colors of red, white and blue. We like the name ORVA with the red swish. See vehicle pictures.
We provide armed guards to various departments of the federal government including : Civic Shield Bureau, National Guardpost Agency, All of the armed forces Navy , Air Force, Army, Coast Guard.

Target Market(s)

Federal government, all the armed forces , large government contractors in the security industry

Contact Information for Business Card

we want a QR code linking to our website

Logo Text

I want our name ORVA in the logo with the red white and blue color scheme srr pictures of our vehicles

Colors
ec1f27
ffffff
0255a3

Requirements
Must have
• name, position title, 2 or 3 phone numbers, e mail address
Nice to have
• some foil
Should not have
• n/a

```html
<!DOCTYPE html>
<html lang="en">
<head>
<meta charset="utf-8">
<title>ORVA Stationery</title>
<link href="https://fonts.googleapis.com/css2?family=Open+Sans:wght@400;600;800&family=Arimo:wght@400&display=swap" rel="stylesheet">
<style>
  :root{
    --red:#ec1f27;
    --blue:#0255a3;
    --white:#ffffff;
    --ink:#4a4a4a;
    --ink-dark:#222222;
    --stage:#e4e4e4;
    --flap:#f0f0f0;
    --flap-line:#c9c9c9;
  }
  *{margin:0;padding:0;box-sizing:border-box}
  html,body{width:1200px;height:1200px;overflow:hidden}
  body{background:var(--stage);position:relative;font-family:"Open Sans",Arial,sans-serif;color:var(--ink)}

  .sheet{position:absolute;background:var(--white);box-shadow:0 2px 8px rgba(0,0,0,.18);overflow:hidden}
  .band{position:absolute;left:0;width:100%;display:block}

  /* letterhead */
  .letterhead{left:120px;top:280px;width:556px;height:712px}
  .letterhead .band-top{top:0;height:40px}
  .letterhead .band-bottom{bottom:0;height:30px}
  .brand{position:absolute;font-family:"Open Sans",Arial,sans-serif;font-weight:800;color:var(--blue);letter-spacing:2px;line-height:1}
  .letterhead .brand{left:54px;top:30px;font-size:34px}
  .letter{position:absolute;left:53px;top:128px;width:450px;font-size:8.7px;line-height:1.25}
  .letter .date{margin-bottom:9px}
  .letter .recipient{margin-bottom:29px}
  .letter .salutation{margin-bottom:20px}
  .letter p.body{line-height:16px;text-align:justify;margin-bottom:11px;font-size:8.9px}
  .letter .closing{margin-top:30px}
  .signature{display:block;width:130px;height:16px;margin:9px 0 8px;background:linear-gradient(90deg,rgba(60,60,60,.25),rgba(60,60,60,.08))}
  .signer{font-size:10.6px;color:var(--ink-dark);font-weight:600;margin-bottom:3px}
  .role{font-size:8.9px}

  .contacts{position:absolute;left:42px;top:650px;font-family:"Arimo",Arial,sans-serif;font-size:8.7px;color:var(--ink-dark);line-height:10.8px;list-style:none}
  .contacts li{display:flex;align-items:center;gap:4px}
  .contacts svg{width:7px;height:7px;fill:var(--blue);flex:none}
  .contacts .domain{color:var(--blue)}
  .address{position:absolute;right:29px;top:659px;text-align:right;font-family:"Arimo",Arial,sans-serif;font-size:8.7px;color:var(--ink-dark);line-height:10.8px}

  /* envelope front */
  .envelope-front{left:716px;top:493px;width:433px;height:217px}
  .envelope-front .band-top{top:0;height:26px}
  .envelope-front .brand{left:37px;top:20px;font-size:24px;letter-spacing:1.5px}
  .return-rule{position:absolute;left:28px;top:187px;width:369px;height:1.5px;background:var(--blue)}
  .return-address{position:absolute;left:26px;top:194px;font-family:"Arimo",Arial,sans-serif;font-size:8px;color:var(--ink-dark)}

  /* envelope back */
  .envelope-back{left:716px;top:743px;width:430px;height:214px;box-shadow:0 2px 6px rgba(0,0,0,.2)}
  .flap{position:absolute;left:0;top:0;width:100%;height:52px}
</style>
</head>
<body>

<section class="sheet letterhead">
  <svg class="band band-top" viewBox="0 0 556 40" preserveAspectRatio="none">
    <rect x="0" y="0" width="556" height="13" fill="var(--red)"/>
    <path d="M0 13 H556 V17 Q300 20 0 32 Z" fill="var(--blue)"/>
  </svg>
  <div class="brand">ORVA</div>

  <div class="letter">
    <div class="date">Issuing Date: May 5, 2018</div>
    <div class="recipient">Name Of Employee Mr. XYZABC<br>Address of Employee<br>Address Line 2 etc..</div>
    <div class="salutation">Dear Mr.XYZABC</div>
    <p class="body">Lorem Ipsum has been the industry's standard dummy text ever since the 1500s, when an unknown printer took a galley of type and scrambled it to make a type specimen book. It has survived not only five centuries, but also the leap into electronic typesetting, remaining essentially unchanged. It was popularised in the 1960s with the release of Fontline sheets containing Lorem Ipsum passages, and more recently with desktop publishing software like Pressmark Layout including versions of Lorem Ipsum.</p>
    <p class="body">Lorem Ipsum is simply dummy text of the printing and typesetting industry. Lorem Ipsum has been the industry's standard dummy text ever since the 1500s, when an unknown printer took a galley of type and scrambled it to make a type specimen book.</p>
    <p class="body">It has survived not only five centuries, but also the leap into electronic typesetting, remaining essentially unchanged. It was popularised in the 1960s with the release of Fontline sheets containing Lorem IpsumIpsum passages.</p>
    <div class="closing">Yours Sincerely</div>
    <span class="signature" role="img" aria-label="Handwritten signature of Marcus Hale"></span>
    <div class="signer">Marcus Hale</div>
    <div class="role">Managing Director</div>
  </div>

  <ul class="contacts">
    <li><svg viewBox="0 0 10 10"><path d="M1 3 Q5 0 9 3 L8 4.5 L6.5 3.8 L6.5 3 Q5 2.5 3.5 3 L3.5 3.8 L2 4.5 Z M2.5 5 H7.5 L8.5 9 H1.5 Z"/></svg><span>(555) 014-2290 | (555) 017-6631</span></li>
    <li><svg viewBox="0 0 10 10"><path d="M2.5 0.5 H7.5 V9.5 H2.5 Z M3.5 1.5 V7.5 H6.5 V1.5 Z" fill-rule="evenodd"/></svg><span>(555) 014-2290</span></li>
    <li><svg viewBox="0 0 10 10"><path d="M0.5 2 H9.5 V8 H0.5 Z M1.3 2.6 L5 5.4 L8.7 2.6 Z" fill-rule="evenodd"/></svg><span>info@orvaprotective.com</span></li>
    <li><svg viewBox="0 0 10 10"><circle cx="5" cy="5" r="4.5"/></svg><span>www.<span class="domain">orvaprotective</span>.com</span></li>
  </ul>
  <div class="address">4821 Harbor Point Dr Ste. 310<br>Linden, TX 75563</div>

  <svg class="band band-bottom" viewBox="0 0 556 30" preserveAspectRatio="none">
    <path d="M0 22 Q300 16 556 8 V21 H0 Z" fill="var(--blue)"/>
    <rect x="0" y="23" width="556" height="7" fill="var(--red)"/>
  </svg>
</section>

<section class="sheet envelope-front">
  <svg class="band band-top" viewBox="0 0 433 26" preserveAspectRatio="none">
    <rect x="0" y="0" width="433" height="9" fill="var(--red)"/>
    <path d="M0 9 H433 V12 Q240 14 0 24 Z" fill="var(--blue)"/>
  </svg>
  <div class="brand">ORVA</div>
  <div class="return-rule"></div>
  <div class="return-address">4821 Harbor Point Dr Ste. 310, Linden, TX 75563</div>
</section>

<section class="sheet envelope-back">
  <svg class="flap" viewBox="0 0 430 52" preserveAspectRatio="none">
    <path d="M0 0 H430 L413 51 H17 Z" fill="var(--flap)" stroke="var(--flap-line)" stroke-width="1"/>
  </svg>
</section>

</body>
</html>
```